Kelvaro.ch is looking for business card letterhead and envelope C5 with WOW effect

We need a strong business card for our company Kelvaro.ch, logo is available. You want a black or dark background on which the logo Stark r% 26 # 252; appears. Letterhead and envelope in C5 format should be in a similar design, but does not have to be We need a strong business card for our company Kelvaro.ch, logo is available. A black or dark background is desired, on which the logo Stark comes across. The letterhead and the envelope in C5 format should have a similar design.

Target Market(s)

Private customers as well as entrepreneurs

Contact Information for Business Card

E-mail: info@kelvaro-example.ch
Web.www.Kelvaro-example.ch
Tel: +41 ( 0 ) 79 482 6037
Adresse:
Lindenweg 14
9406 Tarnbach

Hier kann man Icons verwenden für Email,Tel und Adressse

Font styles to use
Other font styles liked:
• Dubai,bold

Colors

Designer to choose colors to be used in the design.

Requirements
Must have
• WOW effect
Nice to have
• R% 26 # 252; back business card with our service listings. - VEHICLE LABELING - SHOP WINDOW LABELING - STICKERS AND MUCH MORE ... in red color

```html
<!DOCTYPE html>
<html lang="en">
<head>
<meta charset="utf-8">
<title>Kelvaro.ch – Business Card</title>
<link href="https://fonts.googleapis.com/css2?family=Exo+2:wght@500;800&family=Lato:wght@400&display=swap" rel="stylesheet">
<style>
  :root {
    --backdrop: #707070;
    --card: #050505;
    --card-tint: #161616;
    --accent: #f8c81a;
    --service: #f2c200;
    --white: #ffffff;
    --muted: #d2d2d2;
    --rule: #5a5a5a;
  }
  html, body {
    margin: 0;
    padding: 0;
    width: 1200px;
    height: 1200px;
    overflow: hidden;
    background: var(--backdrop);
  }
  .canvas {
    position: relative;
    width: 1200px;
    height: 1200px;
  }
  .card {
    position: absolute;
    top: 310px;
    background: var(--card);
    box-shadow: 3px 4px 8px rgba(0,0,0,0.45);
    overflow: hidden;
  }
  .card--front { left: 234px; width: 364px; height: 594px; }
  .card--back  { left: 627px; width: 370px; height: 596px; }

  .card__texture {
    position: absolute;
    left: 0; top: 0;
    width: 330px; height: 100%;
    background: linear-gradient(90deg, var(--card-tint) 0%, rgba(22,22,22,0.4) 60%, rgba(5,5,5,0) 100%);
  }

  .brand-name {
    position: absolute;
    margin: 0;
    font-family: "Exo 2", sans-serif;
    font-weight: 800;
    color: var(--white);
    letter-spacing: 1px;
    white-space: nowrap;
  }
  .card--front .brand-name {
    left: 0; right: 0;
    top: 120px;
    text-align: center;
    font-size: 46px;
  }

  .contact-item {
    position: absolute;
    left: 0; right: 0;
    text-align: center;
  }
  .contact-item__icon {
    position: absolute;
    left: 50%;
    transform: translateX(-50%);
    width: 48px; height: 44px;
  }
  .contact-item__rule {
    position: absolute;
    height: 1px;
    width: 52px;
    background: var(--rule);
  }
  .contact-item__rule--left { left: 102px; }
  .contact-item__rule--right { left: 209px; }
  .contact-item__text {
    position: absolute;
    left: 0; right: 0;
    font-family: "Exo 2", sans-serif;
    font-weight: 500;
    font-size: 21px;
    color: var(--muted);
    white-space: nowrap;
  }

  .card--back .brand-mark {
    position: absolute;
    left: 46px; top: 170px;
    width: 64px; height: 64px;
    background: var(--accent);
    border-radius: 50%;
  }
  .card--back .brand-name {
    left: 128px;
    top: 182px;
    font-size: 34px;
  }
  .service-list {
    position: absolute;
    left: 0; right: 0;
    top: 456px;
    margin: 0; padding: 0;
    list-style: none;
    text-align: center;
    font-family: "Lato", sans-serif;
    font-size: 17px;
    line-height: 27px;
    color: var(--service);
  }
</style>
</head>
<body>
<div class="canvas">

  <section class="card card--front">
    <div class="card__texture" role="img" aria-label="Faint dark honeycomb pattern along the left edge"></div>
    <h1 class="brand-name">Kelvaro.ch</h1>

    <div class="contact-item" style="top:225px">
      <span class="contact-item__rule contact-item__rule--left" style="top:22px"></span>
      <svg class="contact-item__icon" viewBox="0 0 48 44" aria-hidden="true">
        <polygon points="12,0 36,0 48,22 36,44 12,44 0,22" fill="var(--accent)"/>
        <path d="M18 13c2-1 3 0 4 2l1 3c0 1-1 2-2 2 1 3 3 5 5 6 0-1 1-2 2-2l3 1c2 1 2 3 1 4-2 3-5 3-8 1-4-3-7-6-8-10-1-3 0-6 2-7z" fill="#111"/>
      </svg>
      <span class="contact-item__rule contact-item__rule--right" style="top:22px"></span>
      <div class="contact-item__text" style="top:52px">+41 ( 0 ) 79 482 6037</div>
    </div>

    <div class="contact-item" style="top:314px">
      <span class="contact-item__rule contact-item__rule--left" style="top:22px"></span>
      <svg class="contact-item__icon" viewBox="0 0 48 44" aria-hidden="true">
        <polygon points="12,0 36,0 48,22 36,44 12,44 0,22" fill="var(--accent)"/>
        <rect x="13" y="14" width="22" height="16" fill="none" stroke="#111" stroke-width="2.2"/>
        <path d="M13 14l11 9 11-9M13 30l8-7M35 30l-8-7" fill="none" stroke="#111" stroke-width="2"/>
      </svg>
      <span class="contact-item__rule contact-item__rule--right" style="top:22px"></span>
      <div class="contact-item__text" style="top:43px">info@kelvaro-example.ch</div>
    </div>

    <div class="contact-item" style="top:389px">
      <span class="contact-item__rule contact-item__rule--left" style="top:22px"></span>
      <svg class="contact-item__icon" viewBox="0 0 48 44" aria-hidden="true">
        <polygon points="12,0 36,0 48,22 36,44 12,44 0,22" fill="var(--accent)"/>
        <g fill="none" stroke="#111" stroke-width="2">
          <circle cx="24" cy="22" r="11"/>
          <ellipse cx="24" cy="22" rx="5" ry="11"/>
          <line x1="13" y1="22" x2="35" y2="22"/>
          <line x1="15" y1="16" x2="33" y2="16"/>
          <line x1="15" y1="28" x2="33" y2="28"/>
        </g>
      </svg>
      <span class="contact-item__rule contact-item__rule--right" style="top:22px"></span>
      <div class="contact-item__text" style="top:49px">www.Kelvaro-example.ch</div>
    </div>

    <div class="contact-item" style="top:471px">
      <span class="contact-item__rule contact-item__rule--left" style="top:22px"></span>
      <svg class="contact-item__icon" viewBox="0 0 48 44" aria-hidden="true">
        <polygon points="12,0 36,0 48,22 36,44 12,44 0,22" fill="var(--accent)"/>
        <path d="M24 35c-5-7-8-11-8-15a8 8 0 0 1 16 0c0 4-3 8-8 15z" fill="#111"/>
        <circle cx="24" cy="20" r="3.2" fill="var(--accent)"/>
      </svg>
      <span class="contact-item__rule contact-item__rule--right" style="top:22px"></span>
      <div class="contact-item__text" style="top:52px">Lindenweg 14,9406 Tarnbach</div>
    </div>
  </section>

  <section class="card card--back">
    <span class="brand-mark" aria-hidden="true"></span>
    <h2 class="brand-name">Kelvaro.ch</h2>
    <ul class="service-list">
      <li>VEHICLE LABELING</li>
      <li>SHOP WINDOW LABELING</li>
      <li>STICKERS AND MUCH MORE ...</li>
    </ul>
  </section>

</div>
</body>
</html>
```